Business Card Design

New business card design

Target Market(s)

Residential & Commercial Property Managers

Industry/Entity Type

Plumbing Services

Contact Information for Business Card

Name - Rowan Keddle, title - Director, Phone Number - 0431 286 517, email - rowan@tbk-plumbing.com.au, Company ABN - 73 215 904 386,

Font styles to use
Sans Serif

Colors
0054AA
0677BA
7BADD7
CADEEF
E8F1F8

```html
<!DOCTYPE html>
<html lang="en">
<head>
<meta charset="utf-8">
<title>TBK Plumbing Services – Business Card</title>
<link rel="stylesheet" href="https://fonts.googleapis.com/css2?family=Roboto:wght@300;400;700&display=swap">
<style>
  :root {
    --backdrop: #26272a;
    --blue-deep: #0054aa;
    --blue-mid: #0677ba;
    --blue-soft: #7badd7;
    --blue-pale: #cadeef;
    --blue-mist: #e8f1f8;
    --blue-bright: #3fb2e0;
    --accent: #1ba0e2;
    --ink: #1b1b1d;
    --ink-soft: #5a5d63;
    --paper: #f7f7f6;
    --band: #1e1f22;
    --band-text: #e6e7e9;
  }
  * { box-sizing: border-box; margin: 0; padding: 0; }
  html, body { width: 1200px; height: 852px; overflow: hidden; }
  body {
    background: var(--backdrop);
    font-family: "Roboto", Arial, sans-serif;
    position: relative;
  }
  .card {
    position: absolute;
    top: 282px;
    width: 504px;
    height: 288px;
    border-radius: 22px;
    overflow: hidden;
    box-shadow: 0 14px 30px rgba(0,0,0,.45);
  }
  .card--front { left: 72px; background: var(--blue-deep); }
  .card--back { left: 624px; background: var(--paper); }

  .card__backdrop {
    position: absolute;
    inset: 0;
    background: linear-gradient(165deg, var(--blue-bright) 0%, var(--blue-mid) 50%, var(--blue-deep) 100%);
  }

  .front-brand {
    position: absolute;
    left: 0; right: 0; top: 118px;
    text-align: center;
    color: #ffffff;
    font-weight: 300;
    font-size: 34px;
    letter-spacing: 2px;
  }

  .back-brand {
    position: absolute;
    left: 34px; top: 40px;
    color: var(--ink);
    font-weight: 300;
    font-size: 30px;
    letter-spacing: 1.5px;
  }

  .person { position: absolute; left: 34px; top: 150px; }
  .person__name { font-weight: 700; font-size: 21px; color: var(--ink); letter-spacing: -.3px; }
  .person__title { font-weight: 300; font-size: 13px; color: var(--ink-soft); margin-top: 2px; }

  .location {
    position: absolute; left: 34px; bottom: 22px;
    font-size: 12px; font-weight: 400; color: var(--ink-soft);
  }
  .location__sep { color: var(--accent); margin: 0 6px; }

  .contacts {
    position: absolute; left: 300px; top: 112px;
    list-style: none;
    font-size: 12px; color: var(--ink-soft); font-weight: 400;
  }
  .contacts__item { display: flex; align-items: center; gap: 8px; height: 17px; }
  .contacts__icon { width: 11px; height: 11px; fill: var(--accent); flex: none; }

  .footer-band {
    position: absolute; right: 0; bottom: 0;
    width: 232px; height: 46px;
  }
  .footer-band svg { position: absolute; inset: 0; width: 100%; height: 100%; }
  .footer-band__text {
    position: absolute; right: 20px; top: 15px;
    font-size: 11.5px; color: var(--band-text); font-weight: 400;
  }
</style>
</head>
<body>

<section class="card card--front" aria-label="Business card front">
  <div class="card__backdrop" role="img" aria-label="Layered blue water wave pattern"></div>
  <div class="front-brand">TBK Plumbing Services</div>
</section>

<section class="card card--back" aria-label="Business card back">
  <div class="back-brand">TBK Plumbing Services</div>

  <div class="person">
    <p class="person__name">Rowan Keddle</p>
    <p class="person__title">Director</p>
  </div>

  <p class="location">Sydney<span class="location__sep">|</span>NSW<span class="location__sep">|</span>Australia</p>

  <ul class="contacts">
    <li class="contacts__item">
      <svg class="contacts__icon" viewBox="0 0 12 12" aria-hidden="true"><path d="M2 1h2l1 3-1.3 1a7 7 0 0 0 3.3 3.3L8 7l3 1v2a1 1 0 0 1-1 1A9 9 0 0 1 1 2a1 1 0 0 1 1-1z"/></svg>
      0431 286 517
    </li>
    <li class="contacts__item">
      <svg class="contacts__icon" viewBox="0 0 12 12" aria-hidden="true"><path d="M1 2.5h10v7H1z"/><path d="M1 2.5l5 4 5-4" stroke="#fff" stroke-width=".8" fill="none"/></svg>
      rowan@tbk-plumbing.com.au
    </li>
    <li class="contacts__item">
      <svg class="contacts__icon" viewBox="0 0 12 12" aria-hidden="true"><circle cx="6" cy="6" r="5"/><path d="M1 6h10M6 1c-2.5 3-2.5 7 0 10M6 1c2.5 3 2.5 7 0 10" stroke="#fff" stroke-width=".7" fill="none"/></svg>
      www.tbk-plumbing.com.au
    </li>
    <li class="contacts__item">
      <svg class="contacts__icon" viewBox="0 0 12 12" aria-hidden="true"><path d="M4 1 3 11M9 1 8 11M1 4h10M1 8h10" stroke="var(--accent)" stroke-width="1.3" fill="none"/></svg>
      ABN - 73 215 904 386
    </li>
  </ul>

  <div class="footer-band">
    <svg viewBox="0 0 232 46" preserveAspectRatio="none" aria-hidden="true">
      <path d="M0 46 L10 0 L22 0 L12 46 Z" fill="var(--accent)"/>
      <path d="M16 46 L26 0 L232 0 L232 46 Z" fill="var(--band)"/>
    </svg>
    <span class="footer-band__text">TBK Plumbing Services Pvt Ltd.</span>
  </div>
</section>

</body>
</html>
```